Webdesign für freie Trauungen
Zielgruppe
Webseite für Hochzeitspaare, Trauerende, Bestatter, Interessierte
Aufgabenstellung
Internetseite
Briefing:
Onepager
Internetseite soll wirken:
Modern
Schlank
Klar
Vertrauenserweckend
professionell
Home:
Reden für besondere Momente im Leben
Schrift an Flyer anpassen
REDEN.
ERZÄHLEN.
ERINNERN.
BERÜHREN.
Bild von mir,
Dazu, meine Reden sind:
freundlich
authentisch
ehrlich
einfühlsam
taktvoll
humorvoll
tiefsinnig
tröstend
nett
zugewandt
interessant
nach Euren Wünschen
mit Euren Inhalten
individuell
sehr persönlich
kreativ
wortgewandt
erfahren
Sprechen Sie mich an! ?
FREIE TRAUUNG:
EINFACH HIMMLISCH!
eine Liebesgeschichte erzählen
Sich ein Versprechen geben
JA zueinander sagen
Mit lieben Menschen feiern
wo, wann, wie - das entscheidet Ihr!
Segensfeier - Willkommensfeier:
im Leben willkommen heißen
Was bedeutet der Name des Kindes?
Was wollt Ihr Eurem Kind mitgeben?
Was wünscht Ihr Euch für Euer Kind?
TRAUERFEIER:
an schöne Momente erinnern
Einen Menschen mit Worten lebendig werden lassen
Mit einer persönlichen und bewegenden Ansprache
Mit all dem, was Sie sich wünschen!
REDEN ZU GEBURTSTAGEN:
mit Humor, Witz und Verstand gemeinsam zurück schauen
Und von Träumen und Sehnsüchten erzählen
Reden zum Jubiläum:
gemeinsam zurück schauen
Geleistetes würdigen
Veränderungen verständlich machen
Ausblicke wagen
Biographien:
festhalten, damit nichts von Ihrer Lebensgeschichte verloren geht
Sie erinnern sich und ich schreibe auf
Referenzen:
???? Wie am besten ???
Persönliches Vita:
Studium an der Hohen Akademie Tellbrück:
- Publizistik
Germanistik
Volkswirtschaftslehre
Lateinamerikanistik
Abschluß: Magistra Artium
Freie Rednerin seit 1998
Telefonnummer 015923847261
Email: marlies.Kersten@postfeld.de
Wirk..

```html
<!DOCTYPE html>
<html lang="de">
<head>
<meta charset="utf-8">
<title>KerstenReden – Reden für besondere Momente im Leben</title>
<link rel="stylesheet" href="https://fonts.googleapis.com/css2?family=Fira+Sans:ital,wght@0,300;0,400;0,600;1,300;1,400;1,600&display=swap">
<style>
:root{
  --teal:#5a9591;
  --teal-light:#7fb0ac;
  --ink:#333;
  --text:#666;
  --muted:#b5b5b5;
  --section:#f8f8f8;
  --card:#fff;
  --footer:#4b4b4b;
  --line:#e6e6e6;
}
*{margin:0;padding:0;box-sizing:border-box}
html,body{width:1200px;height:4126px;overflow:hidden}
body{position:relative;background:#fff;font-family:"Fira Sans",sans-serif;font-weight:300;color:var(--text)}
.abs{position:absolute}
.brand{font-family:"Fira Sans",sans-serif;font-weight:400;color:var(--ink);font-size:20px;letter-spacing:.5px;white-space:nowrap}

/* header */
.site-header{left:0;top:0;width:1200px;height:77px;background:#fff;box-shadow:0 1px 3px rgba(0,0,0,.06);z-index:3}
.site-header .brand{left:256px;top:25px}
.nav a{position:absolute;top:30px;font-size:12px;color:#777;text-decoration:none;font-weight:400}
.nav .active{color:var(--teal);border-bottom:2px solid var(--teal);border-top:1px solid #cfe0de;padding:4px 12px 6px;top:23px}

/* hero */
.hero-photo{left:0;top:77px;width:1200px;height:540px;background:linear-gradient(100deg,#8a8a88 0%,#9b9b99 30%,#8d8d8b 60%,#7e7e7c 100%)}
.hero-cut{left:0;top:540px}
.hero-frame{left:606px;top:245px;width:155px;height:172px;border:2px solid #fff;padding:20px 18px;color:#fff;font-size:22px;line-height:33px;font-weight:300}
.hero-claim{left:774px;top:326px;color:#fff;font-size:22px;line-height:23px;font-weight:300;width:150px}
.scroll-down{left:127px;top:602px}

/* word cloud */
.section-title{width:1200px;text-align:center;font-size:26px;color:#555;font-weight:300}
.speaker-photo{left:537px;top:737px;width:128px;height:240px;background:linear-gradient(180deg,#e8dcc0 0%,#d9c9a6 25%,#2c2c2c 45%,#1d1d1d 100%);border-radius:60px 60px 0 0}
.w{position:absolute;white-space:nowrap;line-height:1}
.w.teal{color:var(--teal)}
.w.dark{color:#3a3a3a}
.w.pale{color:var(--muted)}
.w.grey{color:#888}

/* services */
.services{left:0;top:977px;width:1200px;height:1658px;background:var(--section)}
.service-photo{position:absolute;width:387px;height:258px}
.service-card{position:absolute;width:356px;background:var(--card);box-shadow:0 2px 8px rgba(0,0,0,.06);padding:30px 32px;z-index:1}
.service-card h3{font-weight:300;color:var(--teal);font-size:18px;margin-bottom:14px}
.service-card p{font-size:13px;line-height:19px;color:var(--text)}
.service-card .note{color:var(--teal);margin-top:14px}

/* references */
.ref-title{color:var(--teal)}
.quote-mark{left:588px;top:2740px}
.ref-box{left:303px;top:2783px;width:594px;height:181px;border:1px solid var(--line);background:#fff;box-shadow:0 1px 4px rgba(0,0,0,.05);padding:10px 22px;font-size:11px;line-height:17px;font-style:italic;text-align:center;color:#777}
.ref-arrow{top:2888px}
.ref-author{left:0;top:2970px;width:1200px;text-align:center;font-size:14px;color:#555;font-weight:400}
.dots{left:510px;top:3009px;display:flex;gap:12px;align-items:center}
.dots span{width:6px;height:6px;border-radius:50%;background:#c4c4c4}
.dots .on{width:11px;height:11px;background:var(--teal)}
.ghost-name{left:640px;top:2940px;font-size:120px;font-weight:300;color:#f0f0f0;white-space:nowrap;z-index:-1}

/* gallery */
.gallery-photo{position:absolute;top:3132px;height:248px}

/* vita */
.vita-card{left:243px;top:3444px;width:356px;height:441px;background:#fff;box-shadow:0 2px 8px rgba(0,0,0,.06);padding:24px 26px;color:#444}
.vita-card h2{font-weight:300;font-size:25px;color:#444;margin-bottom:10px}
.vita-card .lead{font-size:13px;font-weight:400;margin-bottom:14px}
.vita-card ul{list-style:none;font-size:11px;line-height:18px;margin-bottom:14px}
.vita-card .small{font-size:11px;margin-bottom:16px}
.contact{margin-top:16px;margin-left:-10px;padding:14px 16px;background:#fafafa}
.contact h2{margin-bottom:6px}
.contact-row{display:flex;align-items:flex-start;gap:10px;font-size:13px;line-height:17px;color:#555;margin-bottom:4px}
.contact-row svg{flex:none;margin-top:3px}
.vita-photo{left:599px;top:3444px;width:357px;height:441px;background:linear-gradient(135deg,#d8d2c4 0%,#c9c1ad 40%,#5a6b55 80%,#3e4a3c 100%)}

/* footer */
.footer-shape{left:0;top:3880px}
.footer-brand{left:256px;top:4040px;color:#fff}
.footer-copy{left:455px;top:4050px;font-size:11px;color:#ddd;font-weight:400}
.footer-links{left:819px;top:4050px;font-size:11px;color:#ddd;font-weight:400}
</style>
</head>
<body>

<header class="abs site-header">
  <div class="abs brand">KerstenReden</div>
  <nav class="nav">
    <a class="active" style="left:521px">Start</a>
    <a style="left:583px">Leistungen ▾</a>
    <a style="left:684px">Persönliches Vita</a>
    <a style="left:804px">Referenzen</a>
    <a style="left:892px">Kontakt</a>
  </nav>
</header>

<section>
  <div class="abs hero-photo" role="img" aria-label="Porträt der Rednerin vor grauer Wand"></div>
  <svg class="abs hero-cut" width="1200" height="78" viewBox="0 0 1200 78">
    <polygon points="0,33 1200,50 1200,78 0,78" fill="#e9e9e9"/>
    <polygon points="0,33 1200,78 0,78" fill="#fff"/>
  </svg>
  <div class="abs hero-frame">REDEN.<br>ERZÄHLEN.<br>ERINNERN.<br>BERÜHREN.</div>
  <div class="abs hero-claim">Reden für besondere Momente im Leben</div>
  <svg class="abs scroll-down" width="16" height="12" viewBox="0 0 16 12"><polyline points="2,3 8,9 14,3" fill="none" stroke="#5a9591" stroke-width="2"/></svg>
</section>

<section>
  <h2 class="abs section-title" style="top:664px">Meine Reden sind</h2>
  <div class="abs speaker-photo" role="img" aria-label="Ganzkörperfoto der Rednerin im dunklen Blazer"></div>
  <span class="w pale" style="left:340px;top:784px;font-size:24px;font-weight:600">freundlich</span>
  <span class="w teal" style="left:463px;top:791px;font-size:16px;font-weight:600">humorvoll</span>
  <span class="w grey" style="left:300px;top:828px;font-size:13px;font-style:italic">einfühlsam</span>
  <span class="w dark" style="left:373px;top:824px;font-size:19px;font-style:italic;font-weight:400">mit Euren Inhalten</span>
  <span class="w teal" style="left:330px;top:858px;font-size:21px">wortgewandt</span>
  <span class="w dark" style="left:460px;top:852px;font-size:31px;font-weight:400">nett</span>
  <span class="w dark" style="left:280px;top:897px;font-size:19px">interessant</span>
  <span class="w pale" style="left:380px;top:887px;font-size:29px;font-weight:600;color:#a8a8a8">individuell</span>
  <span class="w dark" style="left:332px;top:935px;font-size:17px;font-style:italic;font-weight:600">erfahren</span>
  <span class="w teal" style="left:404px;top:932px;font-size:21px">authentisch</span>

  <span class="w grey" style="left:655px;top:780px;font-size:29px">kreativ</span>
  <span class="w dark" style="left:756px;top:780px;font-size:30px;font-weight:400">ehrlich</span>
  <span class="w teal" style="left:681px;top:818px;font-size:35px;font-weight:600">sehr persönlich</span>
  <span class="w pale" style="left:689px;top:863px;font-size:16px;font-style:italic">nach Euren Wünschen</span>
  <span class="w dark" style="left:689px;top:888px;font-size:31px">taktvoll</span>
  <span class="w teal" style="left:801px;top:896px;font-size:21px;font-style:italic">tiefsinnig</span>
  <span class="w teal" style="left:692px;top:940px;font-size:15px">tröstend</span>
  <span class="w dark" style="left:755px;top:933px;font-size:22px">zugewandt</span>
</section>

<section class="abs services">
  <h2 class="abs section-title" style="top:48px">Leistungen</h2>

  <div class="service-photo" style="left:569px;top:128px;background:linear-gradient(180deg,#9ab07a 0%,#6f8a45 45%,#f1f1ef 60%,#7d9a4e 100%)" role="img" aria-label="Brautpaar auf einer Wiese"></div>
  <div class="service-card" style="left:243px;top:157px;height:199px">
    <h3>Trau- &amp; Hochzeitsreden</h3>
    <p>EINFACH HIMMLISCH!<br>eine Liebesgeschichte erzählen. Sich ein Versprechen geben. JA zueinander sagen. Mit lieben Menschen feiern.</p>
    <p class="note">wo, wann, wie – das entscheidet Ihr!</p>
  </div>

  <div class="service-photo" style="left:243px;top:430px;background:linear-gradient(180deg,#a9bfcc 0%,#5c7a5a 30%,#8ea3a6 50%,#b692b5 75%,#5e4a3a 100%)" role="img" aria-label="Blumengesteck an einem See"></div>
  <div class="service-card" style="left:599px;top:476px;height:170px">
    <h3>Trauerreden</h3>
    <p>an schöne Momente erinnern. Einen Menschen mit Worten lebendig werden lassen. Mit einer persönlichen und bewegenden Ansprache. Mit all dem, was Sie sich wünschen!</p>
  </div>

  <div class="service-photo" style="left:569px;top:732px;background:linear-gradient(120deg,#3d8c8c 0%,#c94f6d 35%,#e2c24d 60%,#7f9ab0 85%,#9b8c7c 100%)" role="img" aria-label="Bunte Luftballons"></div>
  <div class="service-card" style="left:243px;top:786px;height:150px">
    <h3>Reden zu Geburtstagen</h3>
    <p>mit Humor, Witz und Verstand gemeinsam zurück schauen Und von Träumen und Sehnsüchten erzählen</p>
  </div>

  <div class="service-photo" style="left:243px;top:1035px;background:linear-gradient(180deg,#d6d9dc 0%,#8f9296 35%,#2f2f33 70%,#555 100%)" role="img" aria-label="Feiernde Gruppe mit Konfetti"></div>
  <div class="service-card" style="left:599px;top:1087px;height:150px">
    <h3>Reden zum Jubiläum</h3>
    <p>gemeinsam zurück schauen. Geleistetes würdigen. Veränderungen verständlich machen. Ausblicke wagen</p>
  </div>

  <div class="service-photo" style="left:569px;top:1336px;background:linear-gradient(135deg,#7a6a55 0%,#5a3f34 40%,#3b3431 70%,#8a7b66 100%)" role="img" aria-label="Alte Schreibmaschine und Kaffeetasse"></div>
  <div class="service-card" style="left:243px;top:1391px;height:150px">
    <h3>Biographien</h3>
    <p>festhalten, damit nichts von Ihrer Lebensgeschichte verloren geht.<br>Sie erinnern sich und ich schreibe auf</p>
  </div>
</section>

<section>
  <div class="abs ghost-name">Kersten</div>
  <h2 class="abs section-title ref-title" style="top:2680px">Refrenzen</h2>
  <svg class="abs quote-mark" width="22" height="18" viewBox="0 0 22 18"><path d="M0 18V9C0 4 3 1 8 0l1 2C6 3 5 5 5 8h4v10zM12 18V9c0-5 3-8 8-9l1 2c-3 1-4 3-4 6h4v10z" fill="#5a9591"/></svg>
  <div class="abs ref-box">Liebe Marlies,<br>vielen lieben Dank für diesen wunderschönen Tag auch “ Mit Dir “.<br>Wir sind überwältigt von Eindrücken und Emotionen, so dass nur langsam alles an seinen rechten Platz in unseren Herzen, Seelen und Erinnerungen nimmt. Eine Bitte haben wir noch an dich: da doch so einiges im emotionalen Rummel an uns vorbei gegangen ist, kannst du uns deine Worte schriftlich zumailen? Ich würde gerne nochmal deine uns sehr bewegenden Worte Revue passieren lassen. Das wäre sehr schön. Ich habe von allen Gästen und vom Personal des Landguts nur die höchsten Töne auch bezüglich deiner Worte gehört.<br>Vielen herzlichen Dank schon mal auf diesem Wege.<br>Liebe Grüße S. &amp; M.</div>
  <svg class="abs ref-arrow" style="left:263px" width="22" height="22" viewBox="0 0 22 22"><circle cx="11" cy="11" r="11" fill="#5a9591"/><polyline points="13,6 8,11 13,16" fill="none" stroke="#fff" stroke-width="2"/></svg>
  <svg class="abs ref-arrow" style="left:915px" width="22" height="22" viewBox="0 0 22 22"><circle cx="11" cy="11" r="11" fill="#5a9591"/><polyline points="9,6 14,11 9,16" fill="none" stroke="#fff" stroke-width="2"/></svg>
  <div class="abs ref-author">S. &amp; M.</div>
  <div class="abs dots"><span></span><span></span><span class="on"></span><span></span><span></span><span></span><span></span><span></span><span></span><span></span></div>
</section>

<section>
  <div class="gallery-photo" style="left:0;width:229px;background:linear-gradient(160deg,#d3c7a5 0%,#c8a98f 40%,#2a2a35 75%)" role="img" aria-label="Porträt der Rednerin im gemusterten Kleid"></div>
  <div class="gallery-photo" style="left:245px;width:413px;background:linear-gradient(100deg,#2f3a33 0%,#cbbf9f 40%,#d9d2c2 60%,#2c4436 100%)" role="img" aria-label="Porträt der Rednerin mit Brille"></div>
  <div class="gallery-photo" style="left:674px;width:193px;background:linear-gradient(180deg,#e8e4dc 0%,#d6c4a8 50%,#c8b59a 100%)" role="img" aria-label="Nachdenkliches Porträt der Rednerin"></div>
  <div class="gallery-photo" style="left:883px;width:317px;background:linear-gradient(90deg,#5b5e5f 0%,#d3c7a5 30%,#2f2f33 55%,#d3c7a5 75%,#c23c7a 100%)" role="img" aria-label="Doppelporträt der Rednerin in Lederjacke"></div>
</section>

<section>
  <div class="abs vita-card">
    <h2>Persönliches Vita</h2>
    <p class="lead">Studium an der Hohen Akademie Tellbrück:</p>
    <ul><li>• Publizistik</li><li>• Germanistik</li><li>• Volkswirtschaftslehre</li><li>• Lateinamerikanistik</li></ul>
    <p class="lead">Abschluß:</p>
    <p class="small">Magistra Artium</p>
    <p class="lead">Freie Rednerin seit 1998</p>
    <div class="contact">
      <h2>Kontakt</h2>
      <div class="contact-row"><svg width="10" height="12" viewBox="0 0 10 12"><rect x="2" y="0" width="6" height="12" rx="1" fill="#5a9591"/><rect x="3" y="1.5" width="4" height="8" fill="#fff"/></svg>015923847261</div>
      <div class="contact-row"><svg width="12" height="10" viewBox="0 0 12 10"><rect width="12" height="9" fill="#5a9591"/><polyline points="0,0 6,5 12,0" fill="none" stroke="#fff"/></svg>marlies.Kersten@postfeld.de</div>
      <div class="contact-row"><svg width="12" height="12" viewBox="0 0 12 12"><circle cx="6" cy="6" r="5.5" fill="#5a9591"/><circle cx="6" cy="6" r="2" fill="#fff"/></svg>Wirkungskreis: Aachen, Viersen, Düsseldorf, Krefeld, Erkelenz, Neuss, Köln</div>
    </div>
  </div>
  <div class="abs vita-photo" role="img" aria-label="Nahaufnahme der Rednerin mit Brille"></div>
</section>

<footer>
  <svg class="abs footer-shape" width="1200" height="246" viewBox="0 0 1200 246">
    <polygon points="0,10 1200,60 1200,246 0,246" fill="#4b4b4b"/>
    <polygon points="560,70 1200,35 1200,85" fill="#5a9591"/>
    <polygon points="0,0 1200,35 1200,60 0,10" fill="#5e5e5e"/>
  </svg>
  <div class="abs brand footer-brand">KerstenReden</div>
  <div class="abs footer-copy">© 2021 KerstenReden. Alle Rechte vorbehalten</div>
  <div class="abs footer-links">Impressum / Datenschutz</div>
</footer>

</body>
</html>
```